TALMORK

The business want a professional looking business card. We have a scetch we will add but want the extra upgrade, and would like more suggestions for variations of our business cards.

```html
<!DOCTYPE html>
<html lang="en">
<head>
<meta charset="UTF-8">
<title>TALMORK — Business Card</title>
<link rel="stylesheet" href="https://fonts.googleapis.com/css2?family=Cormorant+Garamond:wght@500;600&family=Roboto:wght@400&display=swap">
<style>
  :root {
    --backdrop: #e4e6ea;
    --card: #141414;
    --gold: #d2bc8a;
    --card-shadow: rgba(0, 0, 0, 0.28);
  }
  * { margin: 0; padding: 0; box-sizing: border-box; }
  html, body { width: 1200px; height: 840px; overflow: hidden; }
  body {
    background: var(--backdrop);
    display: flex;
    align-items: center;
    justify-content: center;
    gap: 40px;
  }
  .card {
    position: relative;
    width: 540px;
    height: 309px;
    background: var(--card);
    color: var(--gold);
    box-shadow: 0 14px 30px var(--card-shadow);
  }

  /* Front */
  .card-front {
    display: flex;
    flex-direction: column;
    align-items: center;
    justify-content: center;
  }
  .brand-name {
    font-family: "Cormorant Garamond", serif;
    font-weight: 600;
    font-size: 62px;
    letter-spacing: 0.18em;
    margin-right: -0.18em;
    line-height: 1;
  }
  .brand-since {
    margin-top: 16px;
    font-family: "Roboto", sans-serif;
    font-size: 15px;
    letter-spacing: 0.55em;
    margin-right: -0.55em;
  }

  /* Back */
  .card-back { padding: 34px 36px; }
  .holder-name {
    font-family: "Cormorant Garamond", serif;
    font-weight: 600;
    font-size: 34px;
    line-height: 1;
  }
  .holder-title {
    margin-top: 8px;
    font-family: "Roboto", sans-serif;
    font-size: 16px;
    letter-spacing: 0.02em;
  }
  .contact-list {
    list-style: none;
    margin-top: 40px;
    font-family: "Roboto", sans-serif;
    font-size: 17px;
  }
  .contact-item {
    display: flex;
    align-items: center;
    gap: 14px;
    margin-bottom: 12px;
  }
  .contact-icon { width: 20px; height: 20px; flex: none; }
  .back-brand {
    position: absolute;
    right: 36px;
    bottom: 32px;
    font-family: "Cormorant Garamond", serif;
    font-weight: 600;
    font-size: 26px;
    letter-spacing: 0.12em;
  }
</style>
</head>
<body>
  <section class="card card-front">
    <div class="brand-name">TALMORK</div>
    <div class="brand-since">SINCE 2026</div>
  </section>

  <section class="card card-back">
    <div class="holder-name">Arne Halvor Solberg</div>
    <div class="holder-title">CEO &amp; FOUNDER</div>

    <ul class="contact-list">
      <li class="contact-item">
        <svg class="contact-icon" viewBox="0 0 20 20" fill="none" stroke="currentColor" stroke-width="1.6">
          <rect x="5" y="1.5" width="10" height="17" rx="2"/>
          <line x1="8.5" y1="15.5" x2="11.5" y2="15.5"/>
        </svg>
        <span>004790418726</span>
      </li>
      <li class="contact-item">
        <svg class="contact-icon" viewBox="0 0 20 20" fill="none" stroke="currentColor" stroke-width="1.6">
          <rect x="1.5" y="4" width="17" height="12"/>
          <polyline points="1.5,4 10,11 18.5,4"/>
        </svg>
        <span>talmork.llc@postbox.com</span>
      </li>
      <li class="contact-item">
        <svg class="contact-icon" viewBox="0 0 20 20" fill="none" stroke="currentColor" stroke-width="1.4">
          <circle cx="10" cy="10" r="8.5"/>
          <ellipse cx="10" cy="10" rx="3.8" ry="8.5"/>
          <line x1="1.5" y1="10" x2="18.5" y2="10"/>
          <line x1="3" y1="5.5" x2="17" y2="5.5"/>
          <line x1="3" y1="14.5" x2="17" y2="14.5"/>
        </svg>
        <span>www.talmork.llc</span>
      </li>
    </ul>

    <div class="back-brand">TALMORK</div>
  </section>
</body>
</html>
```